Appraisal and Umpire Services for Property Damage Insurance Claims

I need a banner design that I can post as an advertisement on industry web pages. I would like this to be elegant and reflective of quality, integrity and professionalism.

Target Market(s)

Insurance Companies and Attorneys

Industry/Entity Type

Insurance

Contact Information for Business Card

Gordon T. Ashby
218 Birchwell Lane
PO Box 913
Clifton Park, NY 12348
gashby@meridaleclaims.com
Phone: (800) 519-4867, Ext. 2716
Direct: (315) 648-9052

Logo Text

Line One: Silver Hollow Claim Service, Inc. Line two: Appraisal and Umpire Services

Font styles to use
Serif
Sans Serif

Colors
0255a3
f78f20
faa54b
3176b5

Requirements
Must have
• New Logo and matching banner, business card and stationary.
• The colors must be orange and navy blue in the logo. I have selected them below.

```html
<!DOCTYPE html>
<html lang="en">
<head>
<meta charset="utf-8">
<title>Silver Hollow Claim Service – Business Card Options</title>
<link href="https://fonts.googleapis.com/css2?family=Montserrat:wght@400;500;700;800&display=swap" rel="stylesheet">
<style>
  :root {
    --navy: #23255f;
    --orange: #f15a29;
    --amber: #f9a33f;
    --ink: #2a2a35;
    --paper: #ffffff;
    --shadow: 0 5px 9px rgba(0,0,0,0.22);
  }
  * { margin: 0; padding: 0; box-sizing: border-box; }
  html, body { width: 1200px; height: 907px; overflow: hidden; background: var(--paper); }
  body { position: relative; font-family: "Montserrat", sans-serif; color: var(--ink); }
  p { line-height: 1; }

  .card {
    position: absolute; width: 398px; height: 221px;
    background: var(--paper); border-radius: 24px;
    box-shadow: var(--shadow); overflow: hidden;
  }
  .card--centered-white { left: 128px; top: 152px; }
  .card--centered-band  { left: 128px; top: 518px; }
  .card--split-white    { left: 666px; top: 53px; }
  .card--split-faint    { left: 666px; top: 341px; }
  .card--split-plain    { left: 666px; top: 646px; }

  /* centered layout */
  .centered { position: absolute; left: 0; right: 0; text-align: center; }
  .wordmark-row {
    top: 19px; display: flex; justify-content: center; align-items: center; gap: 8px;
  }
  .wordmark {
    font-weight: 800; font-size: 30px; letter-spacing: -0.5px; color: var(--navy); line-height: 1;
  }
  .mark-square { width: 15px; height: 15px; background: var(--orange); }
  .rule-navy { position: absolute; height: 1.5px; background: var(--navy); }
  .centered-rule { left: 65px; width: 274px; top: 54px; }
  .company { font-weight: 400; font-size: 16px; letter-spacing: 0.6px; color: var(--ink); }
  .tagline { font-weight: 400; font-size: 11.5px; color: var(--ink); }
  .centered.company { top: 62px; }
  .centered.tagline { top: 88px; }

  .person {
    display: inline-block; font-weight: 700; font-size: 21px; color: var(--navy);
    padding-bottom: 2px; border-bottom: 2px solid var(--orange); line-height: 1.15;
  }
  .centered.person-row { top: 128px; }
  .contact { display: flex; align-items: center; gap: 3px; font-size: 14.5px; font-weight: 400; }
  .centered.contact { justify-content: center; }
  .centered.phone { top: 171px; }
  .centered.email { top: 194px; }
  .icon { width: 15px; height: 15px; flex: none; }

  .band {
    position: absolute; left: 0; right: 0; top: 120px; bottom: 0;
    background: linear-gradient(to bottom, #ee4a26 0%, #f26a2a 55%, var(--amber) 100%);
  }
  .on-orange { color: #fff; }
  .on-orange .person, .person.on-orange { color: #fff; border-bottom-color: #fff; }

  /* split layout */
  .stack { position: absolute; left: 14px; top: 18px; width: 178px; }
  .stack-row { display: flex; align-items: flex-start; gap: 8px; }
  .stack .wordmark { font-size: 34px; line-height: 0.98; letter-spacing: -1px; }
  .stack .mark-square { width: 16px; height: 16px; margin-top: 7px; }
  .stack .company { font-size: 15px; margin-top: 9px; letter-spacing: 0.4px; white-space: nowrap; }
  .stack .rule-navy { position: static; height: 1.5px; width: 168px; margin-top: 4px; }
  .stack .tagline { font-size: 11px; margin-top: 4px; padding-left: 3px; white-space: nowrap; }
  .no-rule .rule-navy { visibility: hidden; }

  .side { position: absolute; left: 195px; right: 0; top: 0; bottom: 0; }
  .side--orange { background: linear-gradient(to bottom, var(--amber) 0%, #f47a2c 50%, #ef4e24 100%); }
  .side-inner { position: absolute; left: 10px; top: 0; right: 0; bottom: 0; }
  .side .person { position: absolute; top: 134px; white-space: nowrap; font-size: 19px; }
  .side .contact { position: absolute; left: 0; white-space: nowrap; font-size: 11px; gap: 3px; }
  .side .contact.phone { top: 177px; }
  .side .contact.email { top: 196px; }
  .side .icon { width: 12px; height: 12px; }

  .faint-name {
    position: absolute; left: 10px; top: 18px; color: rgba(255,255,255,0.14);
    font-weight: 800; font-size: 34px; line-height: 0.98; letter-spacing: -1px;
  }
  .faint-company {
    position: absolute; left: 10px; top: 100px; color: rgba(255,255,255,0.14);
    font-size: 15px; letter-spacing: 0.4px; white-space: nowrap;
  }
</style>
</head>
<body>

<svg width="0" height="0" style="position:absolute" aria-hidden="true">
  <defs>
    <symbol id="i-phone" viewBox="0 0 16 16">
      <circle cx="8" cy="8" r="8" fill="#f26a2a"/>
      <path d="M5.3 3.6l1.4 1.9-.8 1c.5 1.3 1.4 2.2 2.6 2.7l1-.8 1.9 1.4-.6 1.5c-3.4.1-6.6-3-6.9-6.4z" fill="#fff"/>
    </symbol>
    <symbol id="i-mail" viewBox="0 0 16 16">
      <circle cx="8" cy="8" r="8" fill="#f26a2a"/>
      <rect x="3.6" y="5" width="8.8" height="6" rx="0.6" fill="#fff"/>
      <path d="M3.8 5.3L8 8.5l4.2-3.2" fill="none" stroke="#f26a2a" stroke-width="0.9"/>
    </symbol>
  </defs>
</svg>

<!-- Option 1: centered, white -->
<section class="card card--centered-white">
  <div class="centered wordmark-row"><span class="wordmark">SILVER HOLLOW</span><span class="mark-square"></span></div>
  <div class="rule-navy centered-rule"></div>
  <p class="centered company">CLAIM SERVICE, INC</p>
  <p class="centered tagline">Appraisal and Umpire Services</p>
  <div class="centered person-row"><span class="person">Gordon T. Ashby</span></div>
  <p class="centered contact phone"><svg class="icon"><use href="#i-phone"/></svg>(800) 519-4867, Ext. 2716</p>
  <p class="centered contact email"><svg class="icon"><use href="#i-mail"/></svg>gashby@meridaleclaims.com</p>
</section>

<!-- Option 2: centered, orange band -->
<section class="card card--centered-band">
  <div class="centered wordmark-row"><span class="wordmark">SILVER HOLLOW</span><span class="mark-square"></span></div>
  <div class="rule-navy centered-rule"></div>
  <p class="centered company">CLAIM SERVICE, INC</p>
  <p class="centered tagline">Appraisal and Umpire Services</p>
  <div class="band"></div>
  <div class="centered person-row on-orange"><span class="person">Gordon T. Ashby</span></div>
  <p class="centered contact phone on-orange"><svg class="icon"><use href="#i-phone"/></svg>(800) 519-4867, Ext. 2716</p>
  <p class="centered contact email on-orange"><svg class="icon"><use href="#i-mail"/></svg>gashby@meridaleclaims.com</p>
</section>

<!-- Option 3: split, white -->
<section class="card card--split-white">
  <div class="stack">
    <div class="stack-row"><span class="wordmark">SILVER<br>HOLLOW</span><span class="mark-square"></span></div>
    <p class="company">CLAIM SERVICE, INC</p>
    <div class="rule-navy"></div>
    <p class="tagline">Appraisal and Umpire Services</p>
  </div>
  <div class="side"><div class="side-inner">
    <span class="person">Gordon T. Ashby</span>
    <p class="contact phone"><svg class="icon"><use href="#i-phone"/></svg>(800) 519-4867, Ext. 2716</p>
    <p class="contact email"><svg class="icon"><use href="#i-mail"/></svg>gashby@meridaleclaims.com</p>
  </div></div>
</section>

<!-- Option 4: split, orange panel with faint name -->
<section class="card card--split-faint">
  <div class="stack no-rule">
    <div class="stack-row"><span class="wordmark">SILVER<br>HOLLOW</span><span class="mark-square"></span></div>
    <p class="company">CLAIM SERVICE, INC</p>
    <div class="rule-navy"></div>
    <p class="tagline">Appraisal and Umpire Services</p>
  </div>
  <div class="side side--orange on-orange">
    <span class="faint-name">SILVER<br>HOLLOW</span>
    <span class="faint-company">CLAIM SERVICE, INC</span>
    <div class="side-inner">
      <span class="person">Gordon T. Ashby</span>
      <p class="contact phone"><svg class="icon"><use href="#i-phone"/></svg>(800) 519-4867, Ext. 2716</p>
      <p class="contact email"><svg class="icon"><use href="#i-mail"/></svg>gashby@meridaleclaims.com</p>
    </div>
  </div>
</section>

<!-- Option 5: split, plain orange panel -->
<section class="card card--split-plain">
  <div class="stack no-rule">
    <div class="stack-row"><span class="wordmark">SILVER<br>HOLLOW</span><span class="mark-square"></span></div>
    <p class="company">CLAIM SERVICE, INC</p>
    <div class="rule-navy"></div>
    <p class="tagline">Appraisal and Umpire Services</p>
  </div>
  <div class="side side--orange on-orange">
    <div class="side-inner">
      <span class="person">Gordon T. Ashby</span>
      <p class="contact phone"><svg class="icon"><use href="#i-phone"/></svg>(800) 519-4867, Ext. 2716</p>
      <p class="contact email"><svg class="icon"><use href="#i-mail"/></svg>gashby@meridaleclaims.com</p>
    </div>
  </div>
</section>

</body>
</html>
```